World Wide News and Current Affairs website

We intends to start up a new website which deals on New and Current Affairs.
Attention Designers,
We want a home page design for this project. Our business is based in the United States. Our goal is to become a well known brand.
The website would consist of a category for News, Business and Tech.
The theme should be beautiful and attention seeking. The website would take bulk of it's news from the US, and Europe.
Designers can get inspiration from already existing new websites such as PWJ, KLV, DASKOLM.
All designs should be clean and easy to navigate.

```html
<!DOCTYPE html>
<html lang="en">
<head>
<meta charset="utf-8">
<title>Halloway News</title>
<link href="https://fonts.googleapis.com/css2?family=Open+Sans:wght@400;600;700&display=swap" rel="stylesheet">
<style>
:root{
  --bg:#f3f5f8;
  --card:#ffffff;
  --line:#e2e6eb;
  --blue:#1d6fae;
  --blue-dark:#165a8e;
  --nav-dark:#2b2b2b;
  --ink:#333a40;
  --muted:#7a8188;
  --orange:#e98a1e;
  --footer:#1b1b1b;
  --footer-text:#d9d9d9;
  --green:#2ea043;
  --red:#d33a2c;
}
*{box-sizing:border-box;margin:0;padding:0}
html,body{width:1200px;height:3279px;overflow:hidden}
body{background:var(--bg);font-family:"Open Sans",Arial,sans-serif;color:var(--ink);position:relative;font-size:13px}
.abs{position:absolute}
.card{background:var(--card);border:1px solid var(--line)}
.ph{display:block}
/* header */
.logo{left:96px;top:38px;font-size:34px;font-weight:700;color:var(--ink);letter-spacing:.5px}
.socials{left:738px;top:42px;display:flex;gap:6px}
.socials span{width:24px;height:24px;border-radius:50%;border:1.5px solid var(--blue);display:block}
.search{left:873px;top:36px;width:240px;height:36px;background:#fff;border:1px solid var(--line);font-size:12px;color:var(--muted);padding:9px 14px}
.search svg{position:absolute;right:12px;top:11px}
.nav{left:87px;top:114px;width:1026px;height:52px;background:var(--blue);display:flex;border-bottom:3px solid var(--blue-dark)}
.nav a{color:#fff;text-decoration:none;font-size:12px;text-transform:uppercase;line-height:49px;padding:0 27px}
.nav a.active{background:var(--nav-dark)}
/* hero */
.hero{left:87px;top:188px;width:713px;height:464px;background:linear-gradient(160deg,#c9c3c0,#6b6461 55%,#2d2b2c)}
.hero-cap{position:absolute;left:24px;bottom:22px;color:#fff;width:560px}
.hero-cap h1{font-size:25px;font-weight:700;text-transform:uppercase;margin-bottom:8px}
.hero-cap p{font-size:13px;line-height:1.55}
.hero-arrows{position:absolute;right:0;bottom:0;width:92px;height:110px;background:var(--blue-dark);display:flex;align-items:center;justify-content:center}
.side-top{left:815px;top:188px;width:298px;height:200px;background:linear-gradient(135deg,#5a86b0,#2d5478)}
.side-top p{position:absolute;left:20px;bottom:28px;color:#fff;font-size:13px;line-height:1.45;width:250px}
.side-ad{left:815px;top:409px;width:298px;height:243px;border:2px solid #c9463e;background:linear-gradient(180deg,#f4f4f4,#cfd6dd)}
/* section titles */
.sec-title{display:flex;align-items:center;justify-content:center;gap:20px;color:var(--blue-dark);text-transform:uppercase;font-size:16px}
.sec-title::before,.sec-title::after{content:"";height:1px;background:#cfd5dc;width:150px}
.sec-title.big{font-size:20px}
.sec-title.big::before,.sec-title.big::after{width:240px}
/* feature */
.feature{left:87px;top:728px;width:1026px;height:352px}
.feat-img{left:26px;top:30px;width:398px;height:288px;background:linear-gradient(140deg,#6f8ea6,#3b5266 60%,#243544)}
.date-tag{position:absolute;right:0;top:0;width:56px;height:56px;background:var(--orange);color:#fff;font-size:12px;text-align:center;padding-top:8px;line-height:1.4}
.feat-cap{position:absolute;left:24px;bottom:14px;color:#fff;width:350px}
.feat-cap h3{font-size:16px;font-weight:600;text-transform:uppercase;margin-bottom:8px}
.feat-cap p{font-size:11px;line-height:1.4}
.feat-item{width:270px}
.feat-item p{font-size:13px;line-height:1.6}
.meta{font-size:11px;color:var(--blue);margin-top:8px;padding-bottom:12px;border-bottom:1px solid var(--line)}
.meta i{font-style:normal;color:var(--muted);margin:0 8px}
/* video */
.video{width:210px;height:254px;background:#fff;border:1px solid var(--line)}
.video .thumb{height:166px;position:relative}
.play{position:absolute;left:50%;top:50%;width:38px;height:38px;margin:-19px 0 0 -19px;border:2px solid #fff;border-radius:50%;background:rgba(0,0,0,.25)}
.play::after{content:"";position:absolute;left:14px;top:10px;border-left:12px solid #fff;border-top:8px solid transparent;border-bottom:8px solid transparent}
.video h4{font-size:13px;color:var(--blue);text-align:center;font-weight:600;margin:14px 0 6px;text-transform:uppercase}
.video p{font-size:11px;text-align:center;color:var(--muted);line-height:1.45;padding:0 12px}
/* tech */
.tech{left:87px;top:1487px;width:695px;height:406px}
.tech-row{position:absolute;left:20px;display:flex;gap:30px}
.tech-row .img{width:278px;height:162px;flex:none}
.tech-row h3{font-size:17px;color:var(--blue-dark);font-weight:600;text-transform:uppercase;line-height:1.45}
.stars{color:var(--orange);font-size:12px;letter-spacing:1px}
.stars b{color:#c9ced4;font-weight:400}
.tech-meta{font-size:12px;color:var(--muted);margin:10px 0 12px}
.tech-meta span{margin-left:10px}
.tech-row p{font-size:12px;color:var(--muted);line-height:1.75;width:350px}
/* industry */
.industry{left:87px;top:1967px;width:695px;height:387px}
.lead-title{font-size:15px;color:var(--ink);margin:20px 0 8px}
.body-sm{font-size:11.5px;color:var(--muted);line-height:1.6}
.continue{font-size:14px;color:var(--muted);margin-top:14px}
.ind-item{position:absolute;left:366px;display:flex;gap:12px}
.ind-item .img{width:114px;height:94px;flex:none}
.ind-item p{font-size:11px;color:var(--muted);line-height:1.6;width:196px}
.ind-item .m{font-size:11px;color:var(--muted);margin-top:6px}
/* market watch */
.mwatch{left:87px;top:2427px;width:695px;height:393px}
.mw-col{position:absolute;top:20px;width:305px}
.mw-col .img{height:186px}
/* sidebar */
.side-box{left:815px;width:298px}
.side-head{height:50px;border-bottom:1px solid var(--line);font-size:14px;color:var(--ink);text-transform:uppercase;padding:16px 22px;background:#f7f8fa}
.side-head.blue{color:var(--blue-dark);background:#fff}
.mk-inner{margin:14px 20px;border:1px solid var(--line);height:210px;background:#fff}
.mk-tabs{display:flex;font-size:9px;border-bottom:1px solid var(--line)}
.mk-tabs span{padding:7px 10px;color:var(--ink)}
.mk-tabs span.on{border-bottom:2px solid var(--blue)}
.mk-table{font-size:11px;width:100%;border-collapse:collapse;margin-top:4px}
.mk-table td{padding:3px 8px}
.mk-table td:nth-child(2){text-align:right}
.mk-table td:nth-child(3){text-align:right}
.up{color:var(--green)}.dn{color:var(--red)}
.ca-item{position:absolute;left:20px;display:flex;gap:14px}
.ca-item .img{width:96px;height:94px;flex:none}
.ca-item h5{font-size:12px;font-weight:400;margin-bottom:4px}
.ca-item p{font-size:11px;color:var(--muted);line-height:1.6;margin-top:4px}
.passion-title{left:815px;top:1924px;font-size:16px;text-transform:uppercase;color:var(--ink)}
.passion{left:815px;top:1957px;display:grid;grid-template-columns:repeat(4,70px);gap:6px 6px}
.passion div{height:78px}
.trading ul{list-style:none;padding:18px 22px}
.trading li{font-size:12px;color:var(--ink);height:26.6px;display:flex;align-items:center;gap:18px}
.trading li::before{content:"";width:9px;height:9px;border-radius:50%;border:1.5px solid #9aa1a8;flex:none}
/* footer */
.footer{left:0;top:2916px;width:1200px;height:363px;background:var(--footer);color:var(--footer-text)}
.footer h6{font-size:15px;font-weight:600;color:#fff;text-transform:uppercase;margin-bottom:26px}
.fcol{position:absolute;top:52px}
.fline{display:flex;gap:18px;font-size:12px;margin-bottom:22px;line-height:1.5}
.fline svg{flex:none;margin-top:2px}
.signup p{font-size:11.5px;line-height:1.6;width:290px}
.signup .input{width:286px;height:40px;background:#fff;margin-top:18px;color:#888;font-size:11px;padding:12px 16px}
.signup .btn{margin-top:14px;width:102px;height:40px;background:var(--blue);color:#fff;font-size:12px;text-transform:uppercase;padding:12px 0;text-align:center}
.qlinks li{list-style:none;font-size:12px;margin-bottom:10px}
.soc li{list-style:none;font-size:13px;margin-bottom:17px;display:flex;align-items:center;gap:12px}
.soc li span{width:26px;height:26px;border-radius:50%;border:1.5px solid var(--footer-text)}
.copy{position:absolute;left:0;width:1200px;top:322px;text-align:center;font-size:12px;color:#bfbfbf}
</style>
</head>
<body>

<!-- header -->
<div class="abs logo">HALLOWAY NEWS</div>
<div class="abs socials"><span></span><span></span><span></span><span></span></div>
<div class="abs search">search
  <svg width="14" height="14" viewBox="0 0 14 14"><circle cx="6" cy="6" r="4.5" fill="none" stroke="#333" stroke-width="1.6"/><line x1="9.3" y1="9.3" x2="13" y2="13" stroke="#333" stroke-width="1.8"/></svg>
</div>
<nav class="abs nav">
  <a class="active">Home</a><a>Company News</a><a>Technology News</a><a>Industry News</a><a>Market Watch</a><a>Business and Tech</a><a>Contact Us</a>
</nav>

<!-- hero -->
<div class="abs hero" role="img" aria-label="Modern office lounge with a video wall and hanging lights">
  <div class="hero-cap">
    <h1>Nemo enim ipsam voluptatem quia</h1>
    <p>Lorem ipsum dolor sit amet, consectetur adipiscing elit, sed do eius-<br>mod tempor incididunt ut labore</p>
  </div>
  <div class="hero-arrows">
    <svg width="44" height="24" viewBox="0 0 44 24"><polyline points="12,3 3,12 12,21" fill="none" stroke="#fff" stroke-width="3"/><polyline points="32,3 41,12 32,21" fill="none" stroke="#fff" stroke-width="3"/></svg>
  </div>
</div>
<div class="abs side-top" role="img" aria-label="Hands working on a laptop with a blue tint">
  <p>Lorem ipsum dolor sit amet, consectetur adipiscing elit, sed do eiusmod</p>
</div>
<div class="abs side-ad" role="img" aria-label="Sponsor advertisement panel with software screenshot"></div>

<!-- feature -->
<div class="abs sec-title big" style="left:87px;top:676px;width:1026px">Feature New</div>
<div class="abs card feature">
  <div class="abs feat-img" role="img" aria-label="Colleagues working together at a laptop">
    <div class="date-tag">Nov<br><b style="font-size:14px">25</b></div>
    <div class="feat-cap">
      <h3>Sed ut perspiciatis unde omnis</h3>
      <p>At vero eos et accusamus et iusto odio dignissimos ducimus qui blanditiis praesentium voluptatum deleniti</p>
    </div>
  </div>
  <div class="abs feat-item" style="left:466px;top:30px"><p>Sed ut perspiciatis unde omnis<br>iste natus &nbsp;sit voluptatem</p><div class="meta">3 minutes ago<i>/</i>0 comments</div></div>
  <div class="abs feat-item" style="left:466px;top:137px"><p>Sed ut perspiciatis unde omnis<br>iste natus &nbsp;sit voluptatem</p><div class="meta">3 minutes ago<i>/</i>0 comments</div></div>
  <div class="abs feat-item" style="left:466px;top:242px"><p>Sed ut perspiciatis unde omnis<br>iste natus &nbsp;sit voluptatem</p><div class="meta" style="border:0">3 minutes ago<i>/</i>0 comments</div></div>
  <div class="abs feat-item" style="left:757px;top:30px"><p>Sed ut perspiciatis unde omnis<br>iste natus &nbsp;sit voluptatem</p><div class="meta">3 minutes ago<i>/</i>0 comments</div></div>
  <div class="abs feat-item" style="left:757px;top:137px"><p>Sed ut perspiciatis unde omnis<br>iste natus &nbsp;sit voluptatem</p><div class="meta">3 minutes ago<i>/</i>0 comments</div></div>
  <div class="abs feat-item" style="left:757px;top:242px"><p>Sed ut perspiciatis unde omnis<br>iste natus &nbsp;sit voluptatem</p><div class="meta" style="border:0">3 minutes ago<i>/</i>0 comments</div></div>
</div>

<!-- video news -->
<div class="abs sec-title" style="left:87px;top:1113px;width:695px">Video News</div>
<div class="abs video" style="left:89px;top:1163px"><div class="thumb" role="img" aria-label="Business people reviewing a tablet" style="background:linear-gradient(135deg,#c7d3dd,#5e6f7c)"><span class="play"></span></div><h4>Sed ut perspiciatis</h4><p>Sed ut perspiciatis unde omnis iste voluptatem accusantium dolor</p></div>
<div class="abs video" style="left:330px;top:1163px"><div class="thumb" role="img" aria-label="Office tower against blue sky" style="background:linear-gradient(180deg,#6fa3d6,#b8cfe4)"><span class="play"></span></div><h4>Sed ut perspiciatis</h4><p>Sed ut perspiciatis unde omnis iste voluptatem accusantium dolor</p></div>
<div class="abs video" style="left:569px;top:1163px"><div class="thumb" role="img" aria-label="Business team in a meeting" style="background:linear-gradient(135deg,#b9c7d4,#4a5c6c)"><span class="play"></span></div><h4>Sed ut perspiciatis</h4><p>Sed ut perspiciatis unde omnis iste voluptatem accusantium dolor</p></div>

<!-- technology news -->
<div class="abs sec-title" style="left:87px;top:1440px;width:695px">Technology News</div>
<div class="abs card tech">
  <div class="tech-row" style="top:26px">
    <div class="img" role="img" aria-label="Woman working on a laptop by a brick wall" style="background:linear-gradient(135deg,#9b6a4e,#5a3a2c)"></div>
    <div>
      <h3>Sed ut perspiciatis unde omnis<br>iste natus error sit</h3>
      <div class="tech-meta"><span class="stars" style="margin:0">★★★<b>★★</b></span><span>April 23 2017</span><span>/</span><span>2 comments</span></div>
      <p>Lorem ipsum dolor sit amet, consectetur adipiscing elit, sed do eiod tempor incididunt ut labore et dolore magna aliqua. Ut enim ad minim veniam, quis nostrud exercitation ullamco laboris nisi ut aliquip ex ea commodo consequat.</p>
    </div>
  </div>
  <div class="tech-row" style="top:222px">
    <div class="img" role="img" aria-label="Hands typing on a laptop with floating message icons" style="background:linear-gradient(135deg,#3b7fc4,#0f3f73)"></div>
    <div>
      <h3>Sed ut perspiciatis unde omnis<br>iste natus error sit</h3>
      <div class="tech-meta"><span class="stars" style="margin:0">★★★<b>★★</b></span><span>April 23 2017</span><span>/</span><span>2 comments</span></div>
      <p>Lorem ipsum dolor sit amet, consectetur adipiscing elit, sed do eiod tempor incididunt ut labore et dolore magna aliqua. Ut enim ad minim veniam, quis nostrud exercitation ullamco laboris nisi ut aliquip ex ea commodo consequat.</p>
    </div>
  </div>
</div>

<!-- industry news -->
<div class="abs sec-title" style="left:87px;top:1918px;width:695px">Industry News</div>
<div class="abs card industry">
  <div class="abs" style="left:20px;top:20px;width:317px">
    <div class="img" role="img" aria-label="Speaker addressing a conference audience" style="height:186px;background:linear-gradient(135deg,#2d3a4e,#8b7a66 70%,#c9b9a2)"></div>
    <div class="lead-title">Nemo enim ipsam voluptatem quia</div>
    <div class="body-sm">At vero eos et accusamus et iusto odiossimos ducim us qui blanditiis praesentivero eos et accusamus vero eos et accusamus et. At vero eos et accusamus et iusto odiossimos ducim us qui blanditiis praesentivero</div>
    <div class="continue">Continue Reading &gt;&gt;</div>
  </div>
  <div class="ind-item" style="top:20px"><div class="img" role="img" aria-label="People seated in a waiting area" style="background:linear-gradient(135deg,#b9a996,#5d5146)"></div><div><p>At vero eos et accusamus et iusto odiossos ducim us qui blanditiis praesentivero eos et accusamus</p><div class="m">3 minutes ago &nbsp;/ &nbsp;0 comments</div></div></div>
  <div class="ind-item" style="top:140px"><div class="img" role="img" aria-label="Journalist holding a microphone" style="background:linear-gradient(135deg,#d8d8d8,#6a6a6a)"></div><div><p>At vero eos et accusamus et iusto odiossos ducim us qui blanditiis praesentivero eos et accusamus</p><div class="m">3 minutes ago &nbsp;/ &nbsp;0 comments</div></div></div>
  <div class="ind-item" style="top:260px"><div class="img" role="img" aria-label="Speaker at a podium with flags" style="background:linear-gradient(135deg,#2b3b66,#b58a3a)"></div><div><p>At vero eos et accusamus et iusto odiossos ducim us qui blanditiis praesentivero eos et accusamus</p><div class="m">3 minutes ago &nbsp;/ &nbsp;0 comments</div></div></div>
</div>

<!-- market watch -->
<div class="abs sec-title" style="left:87px;top:2382px;width:695px">Market Watch</div>
<div class="abs card mwatch">
  <div class="mw-col" style="left:20px">
    <div class="img" role="img" aria-label="Hand holding a tablet showing charts" style="background:linear-gradient(135deg,#eef2f5,#9bb4c6)"></div>
    <div class="lead-title">Nemo enim ipsam voluptatem quia</div>
    <div class="body-sm">At vero eos et accusamus et iusto odiossimos ducim us qui blanditiis praesentivero eos et accusamus vero eos et accusamus et. At vero eos et accusamus et iusto odiossimos ducim us qui blanditiis praesentivero</div>
    <div class="continue">Continue Reading &gt;&gt;</div>
  </div>
  <div class="mw-col" style="left:363px">
    <div class="img" role="img" aria-label="Hand holding a rising blue bar chart" style="background:linear-gradient(135deg,#dfe9f2,#4d86bd)"></div>
    <div class="lead-title">Nemo enim ipsam voluptatem quia</div>
    <div class="body-sm">At vero eos et accusamus et iusto odiossimos ducim us qui blanditiis praesentivero eos et accusamus vero eos et accusamus et. At vero eos et accusamus et iusto odiossimos ducim us qui blanditiis praesentivero</div>
    <div class="continue">Continue Reading &gt;&gt;</div>
  </div>
</div>

<!-- sidebar: markets -->
<div class="abs card side-box" style="top:1119px;height:302px">
  <div class="side-head">Markets</div>
  <div class="mk-inner">
    <div class="mk-tabs"><span class="on">Stocks</span><span>Bonds</span><span>Currencies</span><span>Commodities</span></div>
    <svg width="256" height="66" viewBox="0 0 256 66" style="display:block">
      <line x1="8" y1="30" x2="222" y2="30" stroke="#e6a7a0" stroke-dasharray="2 2"/>
      <polyline points="8,14 20,18 30,16 40,24 52,22 62,30 74,28 84,34 96,32 108,38 120,36 130,40 142,37 154,42 166,40 178,44 190,41 202,46 214,44 222,48" fill="none" stroke="#d33a2c" stroke-width="1.3"/>
      <text x="226" y="20" font-size="8" fill="#333" font-family="Open Sans,sans-serif">2,356 K</text>
      <text x="240" y="38" font-size="8" fill="#333" font-family="Open Sans,sans-serif">K</text>
      <text x="30" y="62" font-size="7" fill="#888" font-family="Open Sans,sans-serif">10:00am</text>
      <text x="110" y="62" font-size="7" fill="#888" font-family="Open Sans,sans-serif">12:00pm</text>
      <text x="180" y="62" font-size="7" fill="#888" font-family="Open Sans,sans-serif">2:00pm</text>
    </svg>
    <table class="mk-table">
      <tr style="background:#fdf0e4"><td>US 500</td><td>2,348.69</td><td class="dn">-0.30%</td></tr>
      <tr><td>US 30</td><td>20,547.76</td><td class="dn">-0.15%</td></tr>
      <tr><td>UK 100</td><td>7,114.55</td><td class="dn">-0.06%</td></tr>
      <tr><td>JP 225</td><td>18,620.75</td><td class="up">+1.03%</td></tr>
    </table>
  </div>
</div>

<!-- sidebar: current affairs -->
<div class="abs card side-box" style="top:1465px;height:428px">
  <div class="side-head blue">Current Affairs</div>
  <div class="ca-item" style="top:72px"><div class="img" role="img" aria-label="City landmark on a cloudy day" style="background:linear-gradient(180deg,#9bb0c4,#4d5a66)"></div><div><h5>Nemo enim ipsam</h5><div class="stars">★★★<b>★★</b></div><p>Vivamus elementum sem nisi. Lorem ipsum</p></div></div>
  <div class="ca-item" style="top:200px"><div class="img" role="img" aria-label="Stack of coins and banknotes" style="background:linear-gradient(135deg,#d9c8a4,#8a7a5a)"></div><div><h5>Nemo enim ipsam</h5><div class="stars">★★★<b>★★</b></div><p>Vivamus elementum sem nisi. Lorem ipsum</p></div></div>
  <div class="ca-item" style="top:328px"><div class="img" role="img" aria-label="Colourful market stall" style="background:linear-gradient(135deg,#b8453a,#2d4f8a)"></div><div><h5>Nemo enim ipsam</h5><div class="stars">★★★<b>★★</b></div><p>Vivamus elementum sem nisi. Lorem ipsum</p></div></div>
</div>

<!-- sidebar: passion -->
<div class="abs passion-title">What is your passion?</div>
<div class="abs passion">
  <div role="img" aria-label="Portrait photo" style="background:linear-gradient(135deg,#c9d3dc,#7f8c98)"></div>
  <div role="img" aria-label="Portrait photo" style="background:linear-gradient(135deg,#b7a48f,#5c4e42)"></div>
  <div role="img" aria-label="Portrait photo" style="background:linear-gradient(135deg,#d9dde1,#8b9197)"></div>
  <div role="img" aria-label="Portrait photo" style="background:linear-gradient(135deg,#c8d0d8,#5a6878)"></div>
  <div role="img" aria-label="Portrait photo" style="background:linear-gradient(135deg,#cfd6dc,#6f7d89)"></div>
  <div role="img" aria-label="Portrait photo" style="background:linear-gradient(135deg,#e0d6cc,#9a8a7a)"></div>
  <div role="img" aria-label="Portrait photo" style="background:linear-gradient(135deg,#dde2e6,#8c959d)"></div>
  <div role="img" aria-label="Portrait photo" style="background:linear-gradient(135deg,#d4dbe1,#6e7a86)"></div>
</div>

<!-- sidebar: trading news -->
<div class="abs card side-box trading" style="top:2153px;height:372px">
  <div class="side-head blue">Trading News</div>
  <ul>
    <li>Nemo enim ipsam voluptatem</li>
    <li>Sed ut perspiciatis unde</li>
    <li>Neque porro quisquam est,</li>
    <li>Duis aute irure dolor in</li>
    <li>Lorem ipsum dolor sit amet,</li>
    <li>Nemo enim ipsam voluptatem</li>
    <li>Sed ut perspiciatis unde</li>
    <li>Neque porro quisquam est,</li>
    <li>Duis aute irure dolor in</li>
    <li>Lorem ipsum dolor sit amet,</li>
  </ul>
</div>

<!-- footer -->
<footer class="abs footer">
  <div class="fcol" style="left:94px">
    <h6>Contact Us</h6>
    <div class="fline"><svg width="14" height="18" viewBox="0 0 14 18"><path d="M7 1a6 6 0 0 1 6 6c0 4.5-6 10-6 10S1 11.5 1 7a6 6 0 0 1 6-6z" fill="none" stroke="#ddd" stroke-width="1.5"/><circle cx="7" cy="7" r="2" fill="#ddd"/></svg><div>Halloway News<br>Brackley Green, Northfield, Hants</div></div>
    <div class="fline"><svg width="16" height="16" viewBox="0 0 16 16"><path d="M3 1l3 3-2 2c1 2 3 4 5 5l2-2 3 3-2 2C7 14 2 9 1 3z" fill="#ddd"/></svg><div>Phone : +44(0)20 5550 1827</div></div>
    <div class="fline"><svg width="16" height="12" viewBox="0 0 16 12"><rect x="1" y="1" width="14" height="10" fill="none" stroke="#ddd" stroke-width="1.4"/><polyline points="1,1 8,7 15,1" fill="none" stroke="#ddd" stroke-width="1.4"/></svg><div>admin@hallowaynews.com</div></div>
  </div>
  <div class="fcol signup" style="left:404px">
    <h6>Sign up to receive email</h6>
    <p>Excepteur sint occaecat cupidatat non proident, sunt in culpa qui Nemo enim ipsam voluptatem</p>
    <div class="input">Enter Name</div>
    <div class="btn">Subscribe</div>
  </div>
  <div class="fcol qlinks" style="left:802px">
    <h6>Quick Links</h6>
    <ul><li>Home</li><li>About Us</li><li>Business and Tech</li><li>Projects</li><li>Blog</li><li>Contact Us</li></ul>
  </div>
  <div class="fcol soc" style="left:1016px">
    <h6>Social</h6>
    <ul><li><span></span>Friendline</li><li><span></span>Chirpwire</li><li><span></span>Circleplus</li><li><span></span>Viewtube</li></ul>
  </div>
  <div class="copy">Copyright © Halloway News 2017. All rights reserved.</div>
</footer>

</body>
</html>
```